Computer Consulting Brochure

Computer Consulting services for schools, small businesses, local governments and medical offices. We design networks, security, monitoring, applications for these environments.
Updates
Project Deadline Extended Reason: I provided a condensed document so as not to overwhelm designers. This document covers only pertinent info that can be further condensed if necessary for physical size constraints. Added Friday, April 7, 2017
Target Market(s)
Schools, Small Businesses, Medical Offices, Local Governments. 4 brochures that are identical except for a section that specifically describes the 4 markets.
Industry/Entity Type
Computer
Colors
Designer to choose colors to be used in the design.
Look and feel
Each slider illustrates characteristics of the customer's brand and the style your logo design should communicate.

```html
<!DOCTYPE html>
<html lang="en">
<head>
<meta charset="utf-8">
<title>Brightline IT – Brochure</title>
<link href="https://fonts.googleapis.com/css2?family=Roboto+Condensed:wght@300;400;700&display=swap" rel="stylesheet">
<style>
:root{
  --teal:#1fa5c4;
  --teal-dark:#168aac;
  --teal-pale:#cfeaf2;
  --orange:#f6ad1b;
  --orange-deep:#ef9a12;
  --yellow-pale:#fbefcf;
  --ink:#3a3a3a;
  --white:#ffffff;
  --page:#ececec;
}
*{margin:0;padding:0;box-sizing:border-box}
html,body{width:1200px;height:1200px;overflow:hidden;background:var(--page)}
body{font-family:"Roboto Condensed",sans-serif;color:var(--ink);position:relative}
.spread{position:absolute;left:220px;width:760px;height:586px;background:var(--white);overflow:hidden;box-shadow:0 2px 8px rgba(0,0,0,.15)}
.spread--outside{top:10px}
.spread--inside{top:604px}
.panel{position:absolute;top:0;width:253.3px;height:586px;overflow:hidden}
.panel--1{left:0}.panel--2{left:253.3px}.panel--3{left:506.6px}
.heading{font-weight:700;color:var(--teal-dark);font-size:18px;letter-spacing:.2px}
.lead{font-weight:700;color:var(--teal-dark);font-size:10.5px;line-height:12.5px}
.bullets{list-style:none}
.bullets li{position:relative;padding-left:9px;font-weight:300;font-size:8.6px;line-height:10.6px;margin-bottom:6px}
.bullets li::before{content:"";position:absolute;left:0;top:3px;width:5px;height:5px;background:var(--teal)}
.bullets--tight li{font-size:8px;line-height:9.6px;margin-bottom:4px}
.photo{position:absolute}
.photo--laptop{left:0;top:370px;width:253.3px;height:216px;background:linear-gradient(160deg,#f4f4f4 0%,#cfd3d6 45%,#8a7a6e 100%)}
.photo--students{left:0;top:60px;width:253.3px;height:210px;background:linear-gradient(120deg,#eef4f6 0%,#9fb7c9 45%,#5d6f8c 100%)}
.photo--classroom{left:0;top:340px;width:506.6px;height:246px;background:linear-gradient(180deg,rgba(255,255,255,0) 0%,#b9cfdc 35%,#7f98b4 100%)}
.block-teal{position:absolute;left:0;top:270px;width:253.3px;height:316px;background:linear-gradient(180deg,var(--teal) 0%,#25a9c7 60%,#1c98b9 100%)}
.block-orange{position:absolute;left:0;top:270px;width:253.3px;height:316px;background:linear-gradient(180deg,var(--orange) 0%,var(--orange-deep) 100%)}
.statement{color:var(--white);font-weight:400;text-transform:uppercase;text-align:center;font-size:13.2px;line-height:19.8px;padding:22px 10px 0}
.contact{position:absolute;left:26px;bottom:12px;color:var(--white);font-size:8.6px;line-height:16px}
.contact div{display:flex;align-items:center;gap:10px}
.contact svg{width:10px;height:10px;flex:none}
.brand{position:absolute;right:16px;top:18px;font-weight:300;font-size:17px;color:var(--teal-dark)}
.cover-title{color:var(--white);text-transform:uppercase;text-align:right;font-weight:400;font-size:28px;line-height:32px;padding:20px 14px 0 0}
.cover-sub{color:var(--white);text-transform:uppercase;text-align:right;font-weight:700;font-size:7.6px;line-height:9.6px;padding:10px 14px 0 0}
.cover-sub p{margin-bottom:6px}
.band{position:absolute;top:0;height:80px}
.band--teal{left:0;width:506.6px;background:linear-gradient(90deg,var(--teal) 0%,#5fbfd6 100%)}
.band--orange{left:506.6px;width:253.4px;background:var(--orange)}
.band-title{position:absolute;left:20px;top:20px;color:var(--white);font-weight:700;font-size:34px}
.band-title--small{left:16px;top:16px;font-size:15px;line-height:17px;text-transform:uppercase}
.body-copy{font-weight:300;font-size:8.6px;line-height:10.8px;margin-bottom:7px}
.col{position:absolute;top:92px;width:225px}
.col--1{left:16px}
.col--2{left:270px;width:222px}
.col--3{left:522px;width:225px}
.tone-teal{position:absolute;left:0;top:80px;width:253.3px;height:506px;background:linear-gradient(180deg,var(--teal-pale) 0%,#e6f4f8 60%,#ffffff 100%)}
.tone-yellow{position:absolute;left:506.6px;top:80px;width:253.4px;height:506px;background:linear-gradient(180deg,#fdf6e4 0%,var(--yellow-pale) 100%)}
.subhead{font-weight:700;color:var(--orange-deep);font-size:10px;line-height:11.5px;margin-bottom:6px}
.bullets--orange li::before{background:var(--orange)}
.bullets--orange li{margin-bottom:4px}
</style>
</head>
<body>

<section class="spread spread--outside">
  <div class="panel panel--1">
    <div style="position:absolute;left:14px;top:18px;width:226px">
      <h2 class="heading">SCHOOLS</h2>
      <p class="lead" style="margin:6px 0 10px">We create environments structured for educational objectives, tailored for the learning process.</p>
      <ul class="bullets">
        <li>Designed with modular concept, thus offering simplified management. Can easily assimilate new technology as new tools become available</li>
        <li>Can easily monitor network activity for any user - by student ID, employee ID, machine ID, app ID, day/time, internet destination, and others.</li>
        <li>Support the use of multiple display devices</li>
        <li>Can implement desktop virtualization for additional cost savings</li>
        <li>Technology is constantly changing - we are able to keep you tuned and upgraded</li>
        <li>Able to add enhance technology without a major restructuring of the existing environment</li>
        <li>We are able to install environments for all sizes and capacities-school, campus or district</li>
        <li>Install and support wireless systems that provide the latest security</li>
      </ul>
    </div>
    <div class="photo photo--laptop" role="img" aria-label="Photo of hands typing on a laptop keyboard"></div>
  </div>

  <div class="panel panel--2">
    <div style="position:absolute;left:12px;top:18px;width:232px">
      <h2 class="heading">RECENT PROJECTS</h2>
      <ul class="bullets bullets--tight" style="margin-top:8px">
        <li>Resolved a major problem at Harborview University for one of their computer clusters used in their research department.</li>
        <li>Participated in the State of RI twenty million dollar project to upgrade all school environments to provide connectivity for every student on high speed wireless. (1:1 computing)</li>
        <li>Created a Lyrix implementation in a large commercial environment. Designed a Lyrix mail server running on the Nimbus cloud for hundreds of users.</li>
        <li>Provided 24x7 monitoring and support for a large boarding school. Implemented an enterprise wireless LAN for a large campus, a campus wide security camera system and an Orchard tablet mobile device management system.</li>
        <li>Created a CentralDirectory domain and related security for a newly constructed medical office. Connected an ultrasound machine to the IT network and enabled external authorized doctors to securely connect to the server to view ultrasound recordings.</li>
      </ul>
    </div>
    <div class="block-teal">
      <p class="statement">Our solutions for schools, medical/dental, small businesses and auto dealerships are cost effective because they are customized specifically for your environment. Your type of business and end users are critical factors that should be the influencing design parameters</p>
      <div class="contact">
        <div><svg viewBox="0 0 10 10"><circle cx="5" cy="5" r="4.4" fill="none" stroke="#fff" stroke-width="1.1"/><rect x="2.8" y="3" width="4.4" height="3.4" fill="#fff"/></svg>www.BrightlineIT.com</div>
        <div><svg viewBox="0 0 10 10"><circle cx="5" cy="5" r="4.4" fill="none" stroke="#fff" stroke-width="1.1"/><path d="M2.8 3.4h4.4v3.2H2.8zM2.8 3.4L5 5.2 7.2 3.4" fill="none" stroke="#fff" stroke-width=".8"/></svg>info@BrightlineIT.com</div>
        <div><svg viewBox="0 0 10 10"><circle cx="5" cy="5" r="5" fill="#fff"/><path d="M3.3 2.6l1.1 1.4-.6.7c.4.8 1 1.4 1.8 1.8l.7-.6 1.4 1.1-.7.9C4.9 7.8 2.5 5.5 2.4 3.3z" fill="#1fa5c4"/></svg>401-555-0142</div>
        <div><svg viewBox="0 0 10 10"><circle cx="5" cy="5" r="5" fill="#fff"/><path d="M5 2a2 2 0 0 1 2 2c0 1.4-2 3.8-2 3.8S3 5.4 3 4a2 2 0 0 1 2-2z" fill="#1fa5c4"/><circle cx="5" cy="4" r=".7" fill="#fff"/></svg>18 Mill Pond Rd #12 Ashford Falls, RI 02900</div>
      </div>
    </div>
  </div>

  <div class="panel panel--3">
    <div class="brand">Brightline IT</div>
    <div class="photo photo--students" role="img" aria-label="Photo of students working at computers in a classroom"></div>
    <div class="block-orange">
      <h1 class="cover-title">Design,<br>Installation &amp;<br>Management<br>of Computing<br>Environments</h1>
      <div class="cover-sub">
        <p>We can monitor(24x7), design+<br>install or modify</p>
        <p>IT environments customized for schools,<br>medical/dental, small businesses and auto<br>dealerships</p>
        <p>Security camera monitoring systems<br>economically integrated into the IT<br>environment</p>
      </div>
    </div>
  </div>
</section>

<section class="spread spread--inside">
  <div class="tone-teal"></div>
  <div class="tone-yellow"></div>
  <div class="photo photo--classroom" role="img" aria-label="Photo of students at a row of computers in a lab"></div>
  <div class="band band--teal"><h2 class="band-title">WHY OUTSOURCE?</h2></div>
  <div class="band band--orange"><h2 class="band-title band-title--small">What we do<br>for all types of IT<br>environments</h2></div>

  <div class="col col--1">
    <p class="lead" style="margin-bottom:5px">We specialized in IT support at a scale tailored to your exact requirements</p>
    <p class="body-copy">A direct, dedicated IT staff will have either idle time during periods of stability or inadequate resources for those times when problems occur simultaneously.</p>
    <p class="body-copy">By outsourcing to Brightline IT your business will always have the ideal level of support, and therefore never overpay nor be insufficiently prepared to deal with sudden problems that can overwhelm insufficient numbers of staff.</p>
    <p class="body-copy">Because funds are allocated efficiently your business can now afford to capitalize on the most current technology and benefit from all features offered by these newest features.</p>
  </div>

  <div class="col col--2">
    <p class="body-copy">Outsourcing is the better economical choice; there are no overtime hours, paid vacations, morale problems, costs associated with health care and mandatory reporting, and other overhead expenses associated with employees.</p>
    <p class="body-copy">But cost is not the only reason to outsource. Your core business is not IT; therefore outsourcing eliminates the need for your personnel to be proficient in multiple areas, i.e. building specialized skills to support your core businesses and functions as well as accumulating skills enabling them to manage, enhance and maintain the ideal IT environment.</p>
    <p class="body-copy">The elimination of this responsibility allows you to focus on finding and developing personnel skills directly related to your business, and not compromising your core business components.</p>
  </div>

  <div class="col col--3">
    <p class="subhead">Install, customize and support all elements of IT environments</p>
    <p class="body-copy">We analyze your unique business requirements, determining if modifications are cost justified for your existing computing environment.</p>
    <p class="subhead">Design the best combination of hardware and software for your environment</p>
    <p class="body-copy">We specialize in Corvane, Netrelle, Lyrix, Orchard, tablets and smart phones. We are able to structure each solution to the specific type of business to achieve the best returns on investment.</p>
    <p class="subhead">Tailor all components of the entire IT environment</p>
    <p class="body-copy" style="margin-bottom:4px">Install, customize, monitor</p>
    <ul class="bullets bullets--orange">
      <li>desktops</li>
      <li>multiple operating systems (Vistra, Orchard, Lyrix, Sysnix)</li>
      <li>Orchard slates/tablets</li>
      <li>network backbones and their components (Ethernet, fiber, routers, switches, advanced wireless)</li>
      <li>servers</li>
      <li>virtualization (thin clients/zero clients)</li>
      <li>firewalls</li>
      <li>virus/intruder detection</li>
      <li>data encryption</li>
      <li>data analysis and more</li>
    </ul>
  </div>
</section>

</body>
</html>
```